Business cards and stationary design

We just completed the design of our new logo and we need to print new business cards and letterhead for our nonprofit. We are looking for a fresh new design that shows off our new logo. On letterhead, we must have a column on the right or left to include our Board of Directors (up to 45 names) (see attachment)

Industry/Entity Type

Non-Profit

Contact Information for Business Card

Standard business card with name, title, Company name, mailing address phone numbers, email address and website. Tagline on back "Opening doors to safe shelter"

Font styles to use
Sans Serif

Requirements
Must have
• include pertinent information above
• new logo
• fonts compatible with logo
• should use logo colors only
Nice to have
• tag lines

```html
<!DOCTYPE html>
<html lang="en">
<head>
<meta charset="utf-8">
<title>Harbor Shelter Alliance – Business Card</title>
<link href="https://fonts.googleapis.com/css2?family=Michroma&family=Libre+Baskerville&display=swap" rel="stylesheet">
<style>
  :root{
    --teal:#0b7f9c;
    --teal-dark:#0a5b74;
    --red:#e31b23;
    --sky:#a9c9dc;
    --sky-light:#f4f8fb;
    --ink:#3a3a3a;
    --stage:#d7dadd;
    --panel:#e6f0f5;
  }
  *{margin:0;padding:0;box-sizing:border-box}
  html,body{width:1200px;height:1200px;overflow:hidden;background:var(--stage)}
  .card{position:absolute;left:180px;width:840px;height:480px;overflow:hidden;box-shadow:0 6px 18px rgba(0,0,0,.18)}
  .display{font-family:"Michroma",sans-serif;letter-spacing:.12em;text-transform:uppercase;white-space:nowrap}
  .serif{font-family:"Libre Baskerville",serif}

  /* back */
  .card-back{top:90px;background:radial-gradient(ellipse at 45% 50%,var(--sky-light) 0%,#e6eff5 40%,var(--sky) 100%)}
  .back-brand{position:absolute;left:0;right:0;top:190px;text-align:center}
  .back-brand .org-name{color:var(--teal);font-size:28px;display:inline-flex;align-items:center;gap:16px}
  .org-dot{width:16px;height:16px;border-radius:50%;background:var(--red);display:inline-block;flex:none}
  .back-rule{width:520px;height:3px;background:var(--red);margin:16px auto 14px}
  .tagline{color:var(--red);font-size:20px;letter-spacing:.06em;text-transform:uppercase}

  /* front */
  .card-front{top:630px;background:#fff}
  .address-panel{position:absolute;left:580px;top:50px;width:220px;height:230px;background:var(--panel);opacity:.7}
  .front-brand{position:absolute;left:60px;top:72px;display:flex;align-items:center;gap:14px;color:var(--teal);font-size:19px}
  .front-brand-rule{position:absolute;left:90px;top:106px;width:400px;height:3px;background:var(--red)}
  .person{position:absolute;right:46px;top:150px;text-align:right}
  .person-name{color:var(--teal);font-size:19px}
  .person-title{color:var(--ink);font-size:14px;margin-top:6px}
  .address{position:absolute;right:46px;top:218px;text-align:right;color:var(--ink);font-size:16px;line-height:1.55}
  .address-line{display:flex;align-items:center;justify-content:flex-end;gap:8px}
  .divider{position:absolute;left:60px;top:296px;width:740px;height:1px;background:var(--teal)}
  .contact-list{position:absolute;left:70px;top:316px;list-style:none;color:var(--ink);font-size:18px;line-height:1.6}
  .contact-list li{display:flex;align-items:center;gap:12px}
  .icon{width:20px;height:20px;flex:none}
  .bands{position:absolute;left:0;top:0}
</style>
</head>
<body>

<section class="card card-back" aria-label="Card back">
  <div class="back-brand">
    <div class="org-name display"><span class="org-dot"></span>Harbor Shelter Alliance</div>
    <div class="back-rule"></div>
    <p class="tagline serif">Opening doors to safe shelter</p>
  </div>
</section>

<section class="card card-front" aria-label="Card front">
  <div class="address-panel"></div>
  <div class="front-brand display"><span class="org-dot"></span>Harbor Shelter Alliance</div>
  <div class="front-brand-rule"></div>

  <div class="person">
    <div class="person-name display">Marcus Delaney</div>
    <div class="person-title serif">Chairman</div>
  </div>

  <div class="address serif">
    <div class="address-line">P.O Box 208811
      <svg class="icon" viewBox="0 0 20 20"><circle cx="10" cy="10" r="10" fill="var(--teal)"/><path d="M10 4a4 4 0 0 0-4 4c0 3 4 8 4 8s4-5 4-8a4 4 0 0 0-4-4z" fill="#fff"/><circle cx="10" cy="8" r="1.6" fill="var(--teal)"/></svg>
    </div>
    <div class="address-line">Austin, Texas 78701</div>
  </div>

  <div class="divider"></div>

  <ul class="contact-list serif">
    <li><svg class="icon" viewBox="0 0 20 20"><circle cx="10" cy="10" r="10" fill="var(--teal)"/><path d="M7 5l2 2-1 1.5c.6 1.4 1.6 2.4 3 3L12.5 10l2 2-1.5 2C9 13.5 6.5 11 6 6.5z" fill="#fff"/></svg>555.204.3187</li>
    <li><svg class="icon" viewBox="0 0 20 20"><circle cx="10" cy="10" r="10" fill="var(--teal)"/><circle cx="10" cy="10" r="5" fill="none" stroke="#fff" stroke-width="1.2"/><path d="M5 10h10M10 5c-2 3-2 7 0 10M10 5c2 3 2 7 0 10" fill="none" stroke="#fff" stroke-width="1"/></svg>www.harborshelter.org</li>
    <li><svg class="icon" viewBox="0 0 20 20"><circle cx="10" cy="10" r="10" fill="var(--teal)"/><rect x="5" y="6.5" width="10" height="7" fill="#fff"/><path d="M5 6.5l5 4 5-4" fill="none" stroke="var(--teal)" stroke-width="1"/></svg>marcus.harborshelter.org</li>
  </ul>

  <svg class="bands" width="840" height="480" viewBox="0 0 840 480">
    <polygon points="0,480 470,480 470,436 0,462" fill="var(--teal-dark)"/>
    <polygon points="490,480 840,480 840,310 500,310 490,330" fill="var(--teal)"/>
  </svg>
</section>

</body>
</html>
```